Email Marketing Campaign Brief

We want to do an email marketing campaign around our consulting services. The attached documents provide back ground on our work but additional copy can be found below:

KV7lr is committed to helping you, the educator, make informed buying decisions based on local control and independent reviews through a simple, impartial and an effective approach.
In education, there exists a vast array of educational solutions – such as reading, science, language arts, and math curricula; school-wide reform programs; interventions; after-school programs; and new educational technologies. In the marketplace, providers could, and most do, claim to be able to improve educational outcomes and, in many cases, they all pretend to be supported by evidence. But a cursory review reveals that most evidence consists of poorly designed or advocacy-driven studies with some providers having such inadequate research as could only be described as case studies.

So the problem for State and local education officials is that they must sort through a myriad of such claims to decide which solutions merit consideration for their schools and classrooms. One US official stated the problem saying “many of these practitioners have seen interventions (solutions), introduced with great fanfare as being able to produce dramatic gains, come and go over the years, yielding little in the way of positive and lasting change – a perception confirmed by the flat achievement results over the past 30 years in the Federal Survey of Scholastic Attainment long-term trend”

KV7lr is a process by which we make you, the educator, the locus of control

OUR Approach:
With four simple, yet highly effective steps, KV7lr guides educators through an informed buying process that’s based on local control and review.

Step 1 — Research, Review, and Evaluation Criteria

Step 2 — Cost / Benefit Analysis

Step 3 — Education Survey & Culture Scan

Step 4 — Negotiation & Representation

Target Market(s)

Education

Industry/Entity Type

Marketing

Font styles to use
Sans Serif

Colors
f9b46a
f37122

Requirements
Must have
• HTML format that can be used in an Email Campaign
Nice to have
• Additional Copy in Word

```html
<!DOCTYPE html>
<html lang="en">
<head>
<meta charset="utf-8">
<title>KV7lr Email Campaign</title>
<link href="https://fonts.googleapis.com/css2?family=Open+Sans:wght@400;600;700;800&family=Oswald:wght@500;600&display=swap" rel="stylesheet">
<style>
  :root {
    --page: #eceff2;
    --paper: #ffffff;
    --ink: #3a3a3a;
    --ink-soft: #5b5b5b;
    --orange: #f37122;
    --peach: #f9b46a;
    --amber: #f9a11b;
    --red: #d8283c;
    --teal: #1fb5d6;
    --mint: #b9ead6;
    --green: #2e9b78;
    --blue: #1b8fd2;
    --banner: #1e6fb8;
    --hero-a: #f4c9a4;
    --hero-b: #c9a38a;
    --hero-c: #7fa3c4;
  }
  * { box-sizing: border-box; margin: 0; padding: 0; }
  html, body { width: 1200px; height: 1200px; overflow: hidden; }
  body {
    background: var(--page);
    font-family: "Open Sans", Arial, sans-serif;
    color: var(--ink);
    position: relative;
  }
  .email {
    position: absolute; left: 100px; top: 40px;
    width: 1000px; height: 1120px;
    background: var(--paper);
    overflow: hidden;
    box-shadow: 0 4px 18px rgba(0,0,0,.08);
  }
  .topbar { position: absolute; left: 0; top: 0; width: 1000px; height: 44px; }
  .topbar__strip { position: absolute; left: 40px; top: 14px; width: 420px; height: 30px; background: var(--mint); }
  .tabs { position: absolute; right: 40px; top: 0; display: flex; height: 44px; }
  .tab {
    width: 150px; height: 44px;
    display: flex; align-items: center; justify-content: center;
    color: #fff; font-weight: 700; font-size: 18px;
    clip-path: polygon(8% 0, 100% 0, 92% 100%, 0 100%);
    margin-left: -8px;
  }
  .tab--research { background: var(--amber); }
  .tab--policy { background: var(--red); }
  .tab--practice { background: var(--teal); }

  .hero {
    position: absolute; left: 40px; top: 44px; width: 920px; height: 440px;
    background: linear-gradient(120deg, var(--hero-b) 0%, var(--hero-a) 45%, var(--hero-c) 100%);
  }
  .brand {
    position: absolute; left: 20px; top: 64px; width: 400px; height: 96px;
    display: flex; align-items: center; gap: 16px; padding-left: 60px;
    background: var(--orange);
    clip-path: polygon(0 0, 92% 0, 100% 50%, 92% 100%, 0 100%);
    color: #fff; font-weight: 700; font-size: 44px; letter-spacing: 1px;
  }
  .brand__mark { width: 34px; height: 34px; background: #fff; }
  .banner {
    position: absolute; left: 360px; top: 390px; width: 600px; height: 90px;
    background: var(--banner);
    clip-path: polygon(4% 0, 100% 0, 100% 100%, 0 100%);
    color: #fff; padding: 12px 0 0 60px;
  }
  .banner__title { font-weight: 800; font-size: 28px; line-height: 1.1; }
  .banner__sub { font-weight: 600; font-size: 18px; margin-top: 8px; }

  .intro-cols {
    position: absolute; left: 70px; top: 508px; width: 860px;
    display: grid; grid-template-columns: 1fr 1fr; gap: 40px;
    font-size: 13px; line-height: 1.55; color: var(--ink-soft);
  }
  .intro-cols .lead { color: var(--orange); font-weight: 700; }

  .approach { position: absolute; left: 0; top: 668px; width: 1000px; text-align: center; }
  .approach__title { font-weight: 800; font-size: 24px; color: var(--ink); }
  .approach__text { width: 640px; margin: 6px auto 0; font-size: 13px; line-height: 1.5; color: var(--ink-soft); }

  .step { position: absolute; width: 300px; color: #fff; }
  .step svg.step__edge { position: absolute; left: 0; top: -22px; width: 300px; height: 24px; }
  .step__body { height: 100%; padding: 60px 26px 0; }
  .step--one { left: 60px; top: 900px; height: 220px; background: var(--green); }
  .step--two { left: 350px; top: 850px; height: 270px; background: var(--orange); }
  .step--three { left: 640px; top: 800px; height: 320px; background: var(--blue); }
  .step--one .step__edge path { fill: var(--green); }
  .step--two .step__edge path { fill: var(--orange); }
  .step--three .step__edge path { fill: var(--blue); }
  .step__num {
    position: absolute; left: 20px; top: -42px; width: 64px; height: 64px; border-radius: 50%;
    background: #fff; border: 5px solid currentColor;
    display: flex; align-items: center; justify-content: center;
    font-family: "Oswald", "Arial Narrow", sans-serif; font-weight: 600; font-size: 34px;
  }
  .step--one .step__num { color: var(--green); }
  .step--two .step__num { color: var(--orange); }
  .step--three .step__num { color: var(--blue); }
  .step__title {
    font-family: "Oswald", "Arial Narrow", sans-serif; font-weight: 500;
    font-size: 22px; line-height: 1.15; text-transform: uppercase; letter-spacing: .5px;
  }
  .step__list { list-style: none; margin-top: 12px; font-size: 12.5px; line-height: 1.5; }
  .step__list li::before { content: "\2713  "; font-weight: 700; color: var(--peach); }
</style>
</head>
<body>
  <main class="email">
    <header class="topbar">
      <div class="topbar__strip"></div>
      <nav class="tabs">
        <div class="tab tab--research">Research</div>
        <div class="tab tab--policy">Policy</div>
        <div class="tab tab--practice">Practice</div>
      </nav>
    </header>

    <section class="hero" role="img" aria-label="Photo of smiling schoolchildren and a teacher gathered together"></section>

    <div class="brand"><span class="brand__mark"></span>KV7lr</div>

    <div class="banner">
      <div class="banner__title">We help you to build geniuses</div>
      <div class="banner__sub">Research. Teaching. Learning</div>
    </div>

    <section class="intro-cols">
      <p><span class="lead">KV7lr</span> is committed to helping you, the educator, make informed buying decisions based on local control and independent reviews through a simple, impartial and effective approach. In education, there exists a vast array of solutions such as reading, science and math curricula, reform programs and new technologies.</p>
      <p>So the problem for State and local education officials is that they must sort through a myriad of claims to decide which solutions merit consideration for their schools and classrooms. <span class="lead">KV7lr</span> is a process by which we make you, the educator, the locus of control.</p>
    </section>

    <section class="approach">
      <h2 class="approach__title">OUR Approach:</h2>
      <p class="approach__text">With four simple, yet highly effective steps, KV7lr guides educators through an informed buying process that's based on local control and review.</p>
    </section>

    <article class="step step--one">
      <svg class="step__edge" viewBox="0 0 300 24" preserveAspectRatio="none"><path d="M0 24 L0 10 Q40 2 80 12 T160 8 T240 14 T300 6 L300 24 Z"/></svg>
      <div class="step__num">1</div>
      <div class="step__body">
        <h3 class="step__title">Research, Review and Evaluation Criteria</h3>
        <ul class="step__list">
          <li>Define goals with your team</li>
          <li>Review independent evidence</li>
          <li>Set clear evaluation criteria</li>
        </ul>
      </div>
    </article>

    <article class="step step--two">
      <svg class="step__edge" viewBox="0 0 300 24" preserveAspectRatio="none"><path d="M0 24 L0 8 Q50 16 100 6 T200 12 T300 8 L300 24 Z"/></svg>
      <div class="step__num">2</div>
      <div class="step__body">
        <h3 class="step__title">Cost / Benefit Analysis</h3>
        <ul class="step__list">
          <li>Compare full costs of each option</li>
          <li>Weigh expected gains for students</li>
          <li>Rank solutions by value</li>
        </ul>
      </div>
    </article>

    <article class="step step--three">
      <svg class="step__edge" viewBox="0 0 300 24" preserveAspectRatio="none"><path d="M0 24 L0 12 Q40 4 90 10 T180 6 T260 12 T300 4 L300 24 Z"/></svg>
      <div class="step__num">3</div>
      <div class="step__body">
        <h3 class="step__title">Education Survey &amp; Culture Scan</h3>
        <ul class="step__list">
          <li>Survey staff, parents and students</li>
          <li>Scan school culture and readiness</li>
          <li>Share findings with your board</li>
        </ul>
      </div>
    </article>
  </main>
</body>
</html>
```